Coastline Premier Retreats Business Card Design

Design a business card for Coastline Premier Retreats. Look at the website for colors and reference. Card should have logo, name, title, office number, mobile number, email, URL and a tagline like, "Luxury Hotel & Resort Email Marketing" (This might change).

https://www.coastlinepremierretreats.example

The rest I will leave up to your imagination.

Contact Information for Business Card

Logo, name, title, office number, mobile number, email, URL and a tagline like, "Luxury Hotel & Resort Email Marketing" (This might change).

```html
<!DOCTYPE html>
<html lang="en">
<head>
<meta charset="utf-8">
<title>Coastline Premier Retreats – Business Card</title>
<link rel="stylesheet" href="https://fonts.googleapis.com/css2?family=Lato:wght@400;700;900&display=swap">
<style>
  :root {
    --page-bg: #2e2e2e;
    --brand-orange: #e96f1f;
    --brand-orange-deep: #d9621a;
    --card-white: #fbfbfb;
    --card-grey: #e6e6e6;
    --ink: #1b1b1b;
    --text-grey: #5a5a5a;
    --rule: #9a9a9a;
  }
  * { box-sizing: border-box; margin: 0; padding: 0; }
  html, body {
    width: 1200px; height: 900px; overflow: hidden;
    background: var(--page-bg);
    font-family: "Lato", sans-serif;
  }
  .card {
    position: absolute;
    left: 300px;
    width: 600px; height: 343px;
    box-shadow: 0 10px 30px rgba(0,0,0,0.45);
  }
  .card--front {
    top: 86px;
    background: linear-gradient(120deg, var(--brand-orange-deep), var(--brand-orange));
    display: flex; align-items: center; justify-content: center;
  }
  .card--back {
    top: 471px;
    background: linear-gradient(120deg, var(--card-grey), var(--card-white) 60%);
  }
  .wordmark {
    font-weight: 900;
    text-transform: uppercase;
    letter-spacing: 0.04em;
    line-height: 1.05;
  }
  .card--front .wordmark {
    color: #ffffff;
    font-size: 34px;
    text-align: center;
  }
  .card--back .wordmark {
    position: absolute; top: 36px; right: 40px;
    color: var(--ink);
    font-size: 22px;
    text-align: right;
  }
  .person { position: absolute; left: 48px; top: 104px; }
  .person__name {
    color: var(--brand-orange);
    font-weight: 700; font-size: 21px;
    letter-spacing: 0.06em; text-transform: uppercase;
  }
  .person__title, .person__mobile {
    color: var(--text-grey); font-size: 17px; line-height: 1.3;
  }
  .person__mobile { display: flex; align-items: center; gap: 8px; margin-left: 14px; }
  .contact-list {
    position: absolute; left: 62px; top: 188px;
    list-style: none;
  }
  .contact-list li {
    display: flex; align-items: center; gap: 10px;
    color: var(--text-grey); font-size: 16px; height: 23px;
  }
  .icon { width: 14px; height: 14px; flex: none; }
  .divider {
    position: absolute; left: 62px; top: 284px;
    width: 400px; height: 1px; background: var(--rule);
  }
  .tagline {
    position: absolute; left: 62px; top: 296px;
    color: var(--brand-orange);
    font-weight: 700; font-size: 18px;
  }
</style>
</head>
<body>
  <section class="card card--front">
    <div class="wordmark">Coastline<br>Premier Retreats</div>
  </section>

  <section class="card card--back">
    <div class="wordmark">Coastline<br>Premier Retreats</div>

    <div class="person">
      <p class="person__name">Daniel Reyes</p>
      <p class="person__title">Director</p>
      <p class="person__mobile">
        <svg class="icon" viewBox="0 0 14 14"><rect x="3.5" y="1" width="7" height="12" rx="1.2" fill="none" stroke="var(--brand-orange)" stroke-width="1.3"/></svg>
        555.010.0000
      </p>
    </div>

    <ul class="contact-list">
      <li>
        <svg class="icon" viewBox="0 0 14 14"><path d="M3 1.5l2.2 2.6-1.2 1.6a8 8 0 0 0 4.3 4.3l1.6-1.2 2.6 2.2-1.3 1.5C6.5 12.5 1.5 7.5 1.5 2.8z" fill="var(--brand-orange)"/></svg>
        555.014.2200
      </li>
      <li>
        <svg class="icon" viewBox="0 0 14 14"><path d="M7 13.5S2.5 8.5 2.5 5.5a4.5 4.5 0 0 1 9 0c0 3-4.5 8-4.5 8z" fill="var(--brand-orange)"/><circle cx="7" cy="5.5" r="1.6" fill="#fff"/></svg>
        North America
      </li>
      <li>
        <svg class="icon" viewBox="0 0 14 14"><rect x="1" y="3" width="12" height="8" fill="var(--brand-orange)"/><path d="M1 3l6 4.5L13 3" fill="none" stroke="#fff" stroke-width="1.1"/></svg>
        info@coastlinepremierretreats.example
      </li>
      <li>
        <svg class="icon" viewBox="0 0 14 14" fill="none" stroke="var(--brand-orange)" stroke-width="1.1"><circle cx="7" cy="7" r="5.8"/><ellipse cx="7" cy="7" rx="2.6" ry="5.8"/><path d="M1.2 7h11.6M2 4h10M2 10h10"/></svg>
        www.coastlinepremierretreats.example
      </li>
    </ul>

    <div class="divider"></div>
    <p class="tagline">Luxury Hotel &amp; Resort Email Marketing</p>
  </section>
</body>
</html>
```